Interior Design/ New Construction interior finishes

Interior Design Website

Target Market(s)

Home builders, New Construction, Renovations, Public

Industry/Entity Type

Construction

Coding

Coded - Design and coding required

Number of Pages Required

1 page

Font styles to use
Sans Serif

Colors

Designer to choose colors to be used in the design.

Requirements
Must have
• Section to upload pictures of projects
• Simple and modern design
• Designer 1 details about myself
• Logo
• Upload section for photos for future jobs
Nice to have
• Sections they can click on to see certain rooms in a house
• Decorating, floral arrangements, holiday decorating.
• I have lots of before and after as well. Maybe a section for those.

```html
<!DOCTYPE html>
<html lang="en">
<head>
<meta charset="utf-8">
<title>Nova Interiors</title>
<link href="https://fonts.googleapis.com/css2?family=Questrial&display=swap" rel="stylesheet">
<style>
:root{
  --black:#000;
  --dark:#2f2f2f;
  --gold:#f0bd38;
  --gold-soft:#f7d67e;
  --gold-pale:#fcebb8;
  --text:#333;
  --muted:#666;
  --white:#fff;
  --line:#555;
  --chip:#3a3a3a;
}
*{margin:0;padding:0;box-sizing:border-box}
html,body{width:1200px;height:2479px;overflow:hidden}
body{font-family:"Questrial",sans-serif;color:var(--text);background:var(--white);position:relative}

.header{position:absolute;left:0;top:0;width:1200px;height:127px;background:var(--black)}
.brand-mark{position:absolute;left:573px;top:22px;width:54px;height:54px;border:2px solid var(--white);border-radius:50%;background:var(--dark)}
.brand-name{position:absolute;left:0;top:80px;width:1200px;text-align:center;color:var(--white);font-size:19px;letter-spacing:3px;white-space:nowrap}
.call{position:absolute;left:880px;top:42px;color:var(--white);text-align:right;width:160px}
.call small{display:block;font-size:11px;margin-right:42px}
.call strong{display:block;font-weight:400;font-size:16px;margin-right:42px;letter-spacing:.5px;white-space:nowrap}
.call svg{position:absolute;right:0;top:4px}

.nav{position:absolute;left:0;top:127px;width:1200px;height:50px;background:var(--black);border-top:1px solid #444}
.nav ul{list-style:none;position:absolute;left:160px;top:0;height:50px;display:flex;border-left:1px solid var(--line)}
.nav li{height:50px;line-height:50px;text-align:center;color:var(--white);font-size:15px;border-right:1px solid var(--line);white-space:nowrap}
.nav li.active{color:var(--gold)}

.hero{position:absolute;left:0;top:177px;width:1200px;height:499px;background:linear-gradient(180deg,#5b5650 0%,#6d655b 40%,#4c4640 100%)}
.hero h1{position:absolute;left:0;top:135px;width:1200px;text-align:center;color:var(--white);font-weight:400;font-size:50px;line-height:57px;letter-spacing:1px}
.btn-gold{position:absolute;left:527px;top:281px;width:146px;height:44px;background:var(--gold);color:#222;font-size:18px;line-height:44px;text-align:center}
.dots{position:absolute;left:512px;top:459px;display:flex;gap:4px}
.dots span{width:41px;height:4px;background:var(--white)}
.dots span.off{background:transparent;border:1px solid var(--white)}

.features{position:absolute;left:0;top:676px;width:1200px;height:465px}
.card{position:absolute;top:58px;width:274px}
.card .photo{width:274px;height:177px}
.card h3{font-weight:400;font-size:19px;margin-top:23px;letter-spacing:.5px;color:#222}
.card p{font-size:12.5px;line-height:24px;color:var(--muted);margin-top:12px}
.btn-outline{display:block;width:108px;height:37px;border:1px solid #444;text-align:center;line-height:35px;font-size:12.5px;color:#222;margin-top:16px}

.gallery{position:absolute;left:0;top:1141px;width:1200px;height:481px;background:linear-gradient(180deg,#3a3a3a,#2b2b2b)}
.gallery h2{position:absolute;top:62px;width:1200px;text-align:center;color:var(--white);font-weight:400;font-size:34px;letter-spacing:.5px}
.grid{position:absolute;left:162px;top:140px;display:grid;grid-template-columns:repeat(4,216px);grid-template-rows:repeat(2,126px);gap:6px}
.shot{position:relative}
.tag{position:absolute;right:0;top:51px;width:53px;height:21px;background:var(--gold);color:#222;font-size:12px;line-height:21px;text-align:center}
.arrow{position:absolute;top:258px}

.services{position:absolute;left:0;top:1622px;width:1200px;height:458px}
.services h2{position:absolute;top:38px;width:1200px;text-align:center;font-weight:400;font-size:34px;color:#222;letter-spacing:1px}
.service{position:absolute;top:125px;width:300px;text-align:center}
.ring{width:152px;height:152px;margin:0 auto;border:4px solid #222;border-radius:50%;padding:6px;background:var(--white)}
.ring .halo{width:132px;height:132px;border:2px solid var(--gold);border-radius:50%;padding:22px}
.ring .icon{width:84px;height:84px;border-radius:50%;background:radial-gradient(circle at 50% 45%,var(--gold) 0%,var(--gold-soft) 55%,var(--gold-pale) 100%)}
.service h3{font-weight:400;font-size:19px;margin-top:14px;color:#222;letter-spacing:.5px}
.service p{font-size:12.5px;line-height:24px;color:var(--muted);margin-top:10px;padding:0 8px}

.callband{position:absolute;left:0;top:2080px;width:1200px;height:99px;background:var(--gold);text-align:center}
.callband span{display:inline-block;margin-top:33px;font-size:25px;color:#222}
.callband svg{vertical-align:-6px;margin-right:14px}

.footer{position:absolute;left:0;top:2179px;width:1200px;height:300px;background:var(--black);color:var(--white)}
.foot-mark{position:absolute;left:198px;top:40px;width:54px;height:54px;border:2px solid var(--white);border-radius:50%;background:var(--dark)}
.foot-name{position:absolute;left:105px;top:102px;width:240px;text-align:center;font-size:17px;letter-spacing:3px;white-space:nowrap}
.social{position:absolute;left:160px;top:149px;display:flex;gap:8px}
.social span{width:28px;height:28px;border-radius:50%;background:var(--chip);border:1px solid #555;position:relative}
.social span::after{content:"";position:absolute;left:10px;top:10px;width:6px;height:6px;border-radius:50%;background:#ddd}
.col{position:absolute;top:40px}
.col h4{font-weight:400;font-size:15px;margin-bottom:12px;letter-spacing:.5px}
.col li{list-style:none;font-size:12px;line-height:25.6px;color:#ddd;white-space:nowrap}
.foot-rule{position:absolute;left:160px;top:234px;width:880px;height:1px;background:#222}
.copyright{position:absolute;top:260px;width:1200px;text-align:center;font-size:12px;color:#ddd}
</style>
</head>
<body>

<header class="header">
  <div class="brand-mark"></div>
  <div class="brand-name">Nova Interiors</div>
  <div class="call">
    <small>Call Us</small>
    <strong>555 014 2290</strong>
    <svg width="30" height="30" viewBox="0 0 30 30"><circle cx="15" cy="15" r="13.5" fill="none" stroke="#fff" stroke-width="1.5"/><path d="M11 9.5c.6-.6 1.4-.5 1.8.2l1 1.8c.3.6.1 1.2-.4 1.6l-.7.5c.5 1.3 1.6 2.5 2.9 3.1l.5-.7c.4-.5 1.1-.6 1.6-.3l1.8 1c.7.4.8 1.3.2 1.8l-.9.9c-.8.8-2.2.9-3.6.2-2.4-1.2-4.3-3.1-5.4-5.5-.7-1.4-.5-2.8.3-3.6z" fill="#fff"/></svg>
  </div>
</header>

<nav class="nav">
  <ul>
    <li class="active" style="width:110px">Home</li>
    <li style="width:130px">About Us</li>
    <li style="width:124px">Services</li>
    <li style="width:126px">Gallery</li>
    <li style="width:104px">News</li>
    <li style="width:157px">What We Do</li>
    <li style="width:125px">Contact</li>
  </ul>
</nav>

<section class="hero" role="img" aria-label="Living room with white tufted sofas around a rustic wooden coffee table">
  <h1>We Help you Create<br>Great Experience</h1>
  <div class="btn-gold">Get Started</div>
  <div class="dots"><span></span><span></span><span class="off"></span><span></span></div>
</section>

<section class="features">
  <article class="card" style="left:162px">
    <div class="photo" role="img" aria-label="Bedroom with warm lighting" style="background:linear-gradient(160deg,#b8a48c,#7d6a56)"></div>
    <h3>About Us</h3>
    <p>Sed ut perspiciatis unde ovoloreglupatm accusantiumSed ut perspiciatis unde oologlu ptatem accusantium dolorelor miou.</p>
    <span class="btn-outline">Read More</span>
  </article>
  <article class="card" style="left:463px">
    <div class="photo" role="img" aria-label="Living room with stone fireplace" style="background:linear-gradient(160deg,#a88a5e,#5e4a36)"></div>
    <h3>Interior Business</h3>
    <p>Sed ut perspiciatis unde ovoloreglupatm accusantiumSed ut perspiciatis unde oologlu ptatem accusantium dolorelor miou.</p>
    <span class="btn-outline">Read More</span>
  </article>
  <article class="card" style="left:762px">
    <div class="photo" role="img" aria-label="New house with swimming pool" style="background:linear-gradient(180deg,#8fb5d8 0%,#a89478 45%,#3a86b0 75%,#5a8040 100%)"></div>
    <h3>New Construction</h3>
    <p>Sed ut perspiciatis unde ovoloreglupatm accusantiumSed ut perspiciatis unde oologlu ptatem accusantium dolorelor miou.</p>
    <span class="btn-outline">Read More</span>
  </article>
</section>

<section class="gallery">
  <h2>Before &amp; After Gallery</h2>
  <svg class="arrow" style="left:117px" width="20" height="34" viewBox="0 0 20 34"><path d="M17 2L3 17l14 15" fill="none" stroke="#ccc" stroke-width="2.5"/></svg>
  <svg class="arrow" style="left:1056px" width="20" height="34" viewBox="0 0 20 34"><path d="M3 2l14 15L3 32" fill="none" stroke="#ccc" stroke-width="2.5"/></svg>
  <div class="grid">
    <div class="shot" role="img" aria-label="Room under renovation, before" style="background:linear-gradient(160deg,#b0a69a,#6e625a)"><span class="tag">Before</span></div>
    <div class="shot" role="img" aria-label="Finished living room, after" style="background:linear-gradient(160deg,#e4ddd2,#8c7a64)"><span class="tag">After</span></div>
    <div class="shot" role="img" aria-label="Empty room with ladders, before" style="background:linear-gradient(160deg,#dcdcdc,#8a8a8a)"><span class="tag">Before</span></div>
    <div class="shot" role="img" aria-label="Finished bright room, after" style="background:linear-gradient(160deg,#f0ede8,#a6a09a)"><span class="tag">After</span></div>
    <div class="shot" role="img" aria-label="House exterior with scaffolding, before" style="background:linear-gradient(160deg,#7aa050,#9a6a44)"><span class="tag">Before</span></div>
    <div class="shot" role="img" aria-label="Finished house exterior, after" style="background:linear-gradient(160deg,#9ab6d0,#8a6a50)"><span class="tag">After</span></div>
    <div class="shot" role="img" aria-label="Gutted interior, before" style="background:linear-gradient(160deg,#a09484,#5a4a3e)"><span class="tag">Before</span></div>
    <div class="shot" role="img" aria-label="Finished dining room, after" style="background:linear-gradient(160deg,#6a4e38,#c89a6a)"><span class="tag">After</span></div>
  </div>
</section>

<section class="services">
  <h2>What We Do</h2>
  <div class="service" style="left:143px">
    <div class="ring"><div class="halo"><div class="icon" role="img" aria-label="Chandelier icon"></div></div></div>
    <h3>Decorating</h3>
    <p>Sed ut perspiciatis unde ovoloreglupatm accusantiumSed ut perspiciatis unde oologlu ptatem accusantium dolorelor miou.</p>
  </div>
  <div class="service" style="left:450px">
    <div class="ring"><div class="halo"><div class="icon" role="img" aria-label="Floral wreath icon"></div></div></div>
    <h3>Floral Arrangements</h3>
    <p>Sed ut perspiciatis unde ovoloreglupatm accusantiumSed ut perspiciatis unde oologlu ptatem accusantium dolorelor miou.</p>
  </div>
  <div class="service" style="left:757px">
    <div class="ring"><div class="halo"><div class="icon" role="img" aria-label="Beach umbrella and sun icon"></div></div></div>
    <h3>Holiday Decorating</h3>
    <p>Sed ut perspiciatis unde ovoloreglupatm accusantiumSed ut perspiciatis unde oologlu ptatem accusantium dolorelor miou.</p>
  </div>
</section>

<section class="callband">
  <span><svg width="30" height="30" viewBox="0 0 30 30"><path d="M8 4c1-1 2.3-.9 3 .3l2 3.2c.5 1 .2 2-.7 2.7l-1.2.9c1 2.3 2.8 4.2 5.1 5.3l.9-1.2c.7-.9 1.8-1.1 2.7-.6l3.2 1.9c1.2.7 1.3 2.2.4 3.1l-1.6 1.6c-1.4 1.4-3.8 1.6-6.2.4-4-2-7.3-5.3-9.3-9.3C5.1 9.7 5.4 7.3 6.6 5.7z" fill="none" stroke="#222" stroke-width="1.8"/><path d="M18 4a8 8 0 0 1 8 8M18 8a4 4 0 0 1 4 4" fill="none" stroke="#222" stroke-width="1.8"/></svg>Call us on 555 010 3344</span>
</section>

<footer class="footer">
  <div class="foot-mark"></div>
  <div class="foot-name">Nova Interiors</div>
  <div class="social" aria-label="Social links"><span></span><span></span><span></span><span></span></div>
  <div class="col" style="left:372px"><h4>Links</h4><ul><li>Home</li><li>About Us</li><li>News</li><li>Services</li><li>Contact</li></ul></div>
  <div class="col" style="left:512px"><h4>Who we are</h4><ul><li>Sed uterspiciatis</li><li>Perspiciatis unde</li><li>Perspiciatis unde</li><li>Sed uerspiciatem</li><li>Comnisteatusit</li></ul></div>
  <div class="col" style="left:703px"><h4>Projects</h4><ul><li>Sed utersatis</li><li>Perspiciande</li><li>Perspiciatis de</li><li>Sed tiem</li><li>Comnisatusit</li></ul></div>
  <div class="col" style="left:868px"><h4>Contact</h4><ul><li>Sed uterspiciatis dummy 576 lore</li><li>lorem ispm 4867.</li><li>Phone: 555-018-4471</li><li>Email:hello@novainteriors.example</li></ul></div>
  <div class="foot-rule"></div>
  <div class="copyright">© 2018 Nova Interiors.All Rights Reserved. Privacy Policy | Terms of Use | Contact</div>
</footer>

</body>
</html>
```